Business Card for a Dental Office

The design should communicate integrity, quality and reliability. We also want the card look elegant, simple, but still stand out, different from the traditional-dental-office business card.

Industry/Entity Type

Business

```html
<!DOCTYPE html>
<html lang="en">
<head>
<meta charset="utf-8">
<title>Harlow Dental Studio – Business Card</title>
<link rel="stylesheet" href="https://fonts.googleapis.com/css2?family=Oswald:wght@600&family=Arimo:wght@400;700&display=swap">
<style>
  :root {
    --stage: #3a3a3c;
    --ink: #0b0b0b;
    --paper: #ffffff;
    --gold: #d9b92a;
    --gold-deep: #b8961a;
    --text-light: #e9e9e9;
    --text-dark: #111111;
  }
  * { box-sizing: border-box; margin: 0; padding: 0; }
  html, body { width: 1200px; height: 950px; overflow: hidden; }
  body {
    background: var(--stage);
    font-family: "Arimo", Arial, sans-serif;
    position: relative;
  }
  .card {
    position: absolute;
    left: 240px;
    width: 720px;
    height: 410px;
    border-radius: 4px;
    overflow: hidden;
    box-shadow: 0 14px 30px rgba(0,0,0,.45);
  }

  /* Back side */
  .card-back { top: 40px; background: var(--ink); }
  .card-back .brand-mark {
    position: absolute; left: 0; right: 0; top: 140px;
    display: flex; align-items: center; justify-content: center; gap: 14px;
  }
  .card-back .brand-square { width: 34px; height: 34px; background: var(--gold); }
  .card-back .brand-name {
    font-family: "Oswald", Arial, sans-serif; font-weight: 600;
    font-size: 34px; letter-spacing: 1px; text-transform: uppercase;
    color: var(--paper);
  }
  .card-back .website {
    position: absolute; left: 0; right: 0; top: 300px; text-align: center;
    color: var(--text-light); font-size: 15px; letter-spacing: 3px;
  }

  /* Front side */
  .card-front { top: 500px; background: var(--ink); }
  .card-front .top-panel {
    position: absolute; left: 0; top: 0; width: 100%; height: 222px;
    background: var(--paper);
  }
  .card-front .divider {
    position: absolute; left: 0; top: 222px; width: 100%; height: 4px;
    background: var(--gold);
  }
  .front-brand {
    position: absolute; left: 60px; top: 112px;
    display: flex; align-items: center; gap: 14px;
  }
  .front-brand .brand-square { width: 52px; height: 52px; background: var(--gold); }
  .front-brand .brand-name {
    font-family: "Oswald", Arial, sans-serif; font-weight: 600;
    font-size: 32px; line-height: 1; text-transform: uppercase;
    color: var(--text-dark); letter-spacing: .5px;
  }
  .front-brand .tagline {
    margin-top: 4px; font-size: 12.5px; font-weight: 700; letter-spacing: 1.2px;
    text-transform: uppercase; color: var(--gold-deep);
  }
  .person {
    position: absolute; left: 60px; top: 266px; color: var(--text-light);
    font-size: 16px; line-height: 24px;
  }
  .person .name { color: var(--gold); font-weight: 700; font-size: 21px; line-height: 28px; }
  .contacts {
    position: absolute; right: 36px; top: 240px;
    list-style: none; color: var(--text-light); font-size: 15px; line-height: 24px;
  }
  .contacts li { display: flex; align-items: center; justify-content: flex-end; gap: 10px; }
  .contacts svg { width: 15px; height: 15px; fill: var(--gold); flex: none; }
</style>
</head>
<body>

<section class="card card-back" aria-label="Card back">
  <div class="brand-mark">
    <span class="brand-square"></span>
    <span class="brand-name">Harlow Dental Studio</span>
  </div>
  <p class="website">www.harlowdental.com</p>
</section>

<section class="card card-front" aria-label="Card front">
  <div class="top-panel"></div>
  <div class="divider"></div>

  <div class="front-brand">
    <span class="brand-square"></span>
    <div>
      <div class="brand-name">Harlow Dental Studio</div>
      <div class="tagline">Your smile is your gift to others</div>
    </div>
  </div>

  <div class="person">
    <p class="name">Mara Ellison</p>
    <p class="title">President</p>
    <p>2170 Linden Crest Road</p>
    <p>Maple Hollow, NY 11990</p>
  </div>

  <ul class="contacts">
    <li>555 0142 7781
      <svg viewBox="0 0 16 16"><path d="M3 1h3l1.5 4-2 1.2a9 9 0 0 0 4.3 4.3L11 8.5l4 1.5v3a2 2 0 0 1-2 2C6.4 15 1 9.6 1 3a2 2 0 0 1 2-2z"/></svg>
    </li>
    <li>555 0193 4420
      <svg viewBox="0 0 16 16"><path d="M4.5 0h7A1.5 1.5 0 0 1 13 1.5v13a1.5 1.5 0 0 1-1.5 1.5h-7A1.5 1.5 0 0 1 3 14.5v-13A1.5 1.5 0 0 1 4.5 0zM5 2v10h6V2zm3 11a1 1 0 1 0 0 2 1 1 0 0 0 0-2z"/></svg>
    </li>
    <li>555 0167 2094
      <svg viewBox="0 0 16 16"><path d="M4 1h8v4H4zM2 6h12a1 1 0 0 1 1 1v6h-3v2H4v-2H1V7a1 1 0 0 1 1-1zm3 5v3h6v-3z"/></svg>
    </li>
    <li>mara@harlowdental.com
      <svg viewBox="0 0 16 16"><path d="M1 3h14v1.2L8 9 1 4.2zm0 2.6 7 4.8 7-4.8V13H1z"/></svg>
    </li>
  </ul>
</section>

</body>
</html>
```